Business Broker Graphics Package

Hi,

Seeking a smart and professional graphics package design including business card design (double-sided) and letterhead and PowerPoint slide template.

3 Deliverables:

1. Company Letterhead
2. Business Card (two sided) (will consider one sided designs)
3. PowerPoint Template. Requires cover PPT and 2nd page design.

For the prototype use this info:
Marcus Dellorane RPA
Registered Practice Adviser
5678 Harlow Rd.
Tampa, FL 77777
555.014.2273
Demo@Quillbrookpath.com
www.QuillbrookPath.com

I'll give exact information to winner to finalize later.

I've attached the logo..

Business card will be double sided and info for back of card is in attachment.

Look forward to your great ideas and concepts!

Target Market(s)

President's and business owners, CPA's and other professionals.

Industry/Entity Type

Business

Requirements
Nice to have
• Prefer horizontal card, but will consider vertical card design.

The business card should be all or primarily white. Text colors should be same as logo creative combination of black and forest green.

PowerPoint can be white background or lighter palette of colors I like gold color. I do not like darkly colored PowerPoint designs I prefer light and bright designs.

```html
<!DOCTYPE html>
<html lang="en">
<head>
<meta charset="utf-8">
<title>PowerPoint Template Pages – Quillbrook Path</title>
<link rel="stylesheet" href="https://fonts.googleapis.com/css2?family=Montserrat:wght@400;700;800&display=swap">
<style>
  :root {
    --canvas: #f7f7f7;
    --title-light: #b4b4b4;
    --forest: #0d5a2e;
    --forest-deep: #034022;
    --label: #0f3d24;
    --ink: #141414;
    --gold: #c9a649;
    --slide-light: #ececec;
    --slide-mid: #e0e0e0;
    --band-grey: #e2e2e2;
    --cream: #f8f4e8;
    --cream-deep: #efe6cc;
    --sage: #e3eee6;
    --sage-deep: #d2e3d7;
    --watermark: rgba(0, 0, 0, 0.05);
  }
  * { margin: 0; padding: 0; box-sizing: border-box; }
  html, body { width: 1200px; height: 900px; overflow: hidden; }
  body {
    position: relative;
    background: radial-gradient(circle at 50% 45%, #ffffff 0%, var(--canvas) 60%, #ececec 100%);
    font-family: "Montserrat", Arial, sans-serif;
  }
  .sheet-title {
    position: absolute; top: 20px; left: 0; width: 1200px;
    text-align: center; font-size: 29px; letter-spacing: 0.5px;
    color: var(--title-light); font-weight: 400; line-height: 36px;
  }
  .sheet-title strong { color: var(--forest-deep); font-weight: 800; }

  .page-label {
    position: absolute; font-size: 17px; font-weight: 800; line-height: 20px;
    color: var(--label); letter-spacing: 0.3px;
  }

  .slide {
    position: absolute; width: 469px; height: 264px; overflow: hidden;
    background: linear-gradient(160deg, #f3f3f3 0%, var(--slide-light) 55%, var(--slide-mid) 100%);
  }

  .brand {
    position: absolute; display: flex; align-items: center; gap: 6px;
    font-weight: 700; color: var(--ink); white-space: nowrap; line-height: 1;
  }
  .brand-mark { width: 9px; height: 9px; background: var(--forest); flex: none; }

  .watermark {
    position: absolute; left: 0; right: 0; text-align: center;
    white-space: nowrap; font-weight: 400; color: var(--watermark);
    transform: rotate(-12deg); font-size: 38px; letter-spacing: 3px; line-height: 1;
  }

  /* Page 1 */
  .slide--cover-header .header-band {
    position: absolute; left: 0; top: 0; width: 100%; height: 75px;
    background: linear-gradient(180deg, #ededed, #e1e1e1);
    border-bottom: 3px solid var(--forest);
  }
  .slide--cover-header .brand { left: 0; right: 0; justify-content: center; top: 30px; font-size: 20px; }

  /* Page 2 */
  .slide--side-bar .side-bar { position: absolute; left: 0; top: 0; width: 41px; height: 100%; background: var(--forest); }
  .slide--side-bar .title-rule { position: absolute; left: 50px; right: 8px; top: 45px; height: 2px; background: var(--ink); }
  .slide--side-bar .watermark { left: 41px; top: 140px; }
  .slide--side-bar .brand { right: 10px; bottom: 16px; font-size: 13px; }

  /* Page 3 */
  .slide--framed-body { background: var(--band-grey); }
  .slide--framed-body .framed-body {
    position: absolute; left: 0; top: 50px; width: 100%; height: 195px;
    background: linear-gradient(180deg, var(--cream), var(--cream-deep));
    border-top: 4px solid var(--forest); border-bottom: 3px solid var(--forest);
    overflow: hidden;
  }
  .slide--framed-body .watermark { top: 78px; }
  .slide--framed-body .brand { left: 7px; top: 19px; font-size: 13px; }

  /* Page 4 */
  .slide--watermark .watermark { top: 112px; font-size: 40px; }
  .slide--watermark .brand { left: 0; right: 0; justify-content: center; bottom: 14px; font-size: 13px; }

  /* Page 5 */
  .slide--title-block .title-block {
    position: absolute; left: 0; top: 0; width: 100%; height: 211px;
    background: linear-gradient(180deg, var(--sage), var(--sage-deep));
    border-bottom: 4px solid var(--gold);
  }
  .slide--title-block .brand { left: 0; right: 0; justify-content: center; bottom: 15px; font-size: 13px; }
</style>
</head>
<body>
  <h1 class="sheet-title">POWER POINT <strong>TEMPLATE PAGES</strong></h1>

  <span class="page-label" style="left:25px; top:181px;">PAGE 1</span>
  <span class="page-label" style="left:23px; top:481px;">PAGE 2</span>
  <span class="page-label" style="left:24px; top:753px;">PAGE 3</span>
  <span class="page-label" style="left:1104px; top:332px;">PAGE 4</span>
  <span class="page-label" style="left:1104px; top:582px;">PAGE 5</span>

  <section class="slide slide--cover-header" style="left:111px; top:67px;">
    <div class="header-band"></div>
    <div class="brand"><span class="brand-mark"></span>Quillbrook Path</div>
  </section>

  <section class="slide slide--side-bar" style="left:111px; top:348px;">
    <div class="watermark" aria-hidden="true">QUILLBROOK PATH</div>
    <div class="side-bar"></div>
    <div class="title-rule"></div>
    <div class="brand"><span class="brand-mark"></span>Quillbrook Path</div>
  </section>

  <section class="slide slide--framed-body" style="left:111px; top:630px;">
    <div class="framed-body">
      <div class="watermark" aria-hidden="true">QUILLBROOK PATH</div>
    </div>
    <div class="brand"><span class="brand-mark"></span>Quillbrook Path</div>
  </section>

  <section class="slide slide--watermark" style="left:620px; top:208px;">
    <div class="watermark" aria-hidden="true">QUILLBROOK PATH</div>
    <div class="brand"><span class="brand-mark"></span>Quillbrook Path</div>
  </section>

  <section class="slide slide--title-block" style="left:620px; top:489px;">
    <div class="title-block"></div>
    <div class="brand"><span class="brand-mark"></span>Quillbrook Path</div>
  </section>
</body>
</html>
```